BrindleStaffing Business Card Design

We are a staffing company finding positions for dedicated nurses and physicians.

Target Market(s)

Business Professionals

Industry/Entity Type

Staffing

Contact Information for Business Card

Gordon Pratley
Chairman
417 39th Avenue South
SAINT PETERSBURG FL 33712
813-555-4172 Mobile
813-555-8036 Fax
gpratley@brindlestaffing.com
www.brindlestaffing.com

Font styles to use
Sans Serif

Colors
fbee3e
f04a50
f37122

Requirements
Must have
• Logo Attached, see colors below. We'd like to see Yellow, Orange and Red.

```html
<!DOCTYPE html>
<html lang="en">
<head>
<meta charset="utf-8">
<title>BrindleStaffing Business Card</title>
<link rel="stylesheet" href="https://fonts.googleapis.com/css2?family=Roboto:wght@400;500;700&display=swap">
<style>
  :root {
    --bg: #ece9e4;
    --card: #ffffff;
    --yellow: #fbee3e;
    --orange: #f37122;
    --red: #f04a50;
    --ink: #5b5b5b;
    --shadow: rgba(0, 0, 0, 0.18);
  }
  * { margin: 0; padding: 0; box-sizing: border-box; }
  html, body { width: 1200px; height: 1040px; overflow: hidden; }
  body {
    background: var(--bg);
    font-family: "Roboto", Arial, sans-serif;
    position: relative;
  }
  .card {
    position: absolute;
    background: var(--card);
    border-radius: 26px;
    box-shadow: 0 6px 18px var(--shadow);
  }
  .card-front {
    left: 90px; top: 190px;
    width: 400px; height: 660px;
  }
  .card-back {
    left: 560px; top: 340px;
    width: 580px; height: 360px;
    display: flex; align-items: center; justify-content: center;
  }
  .name-block {
    position: absolute;
    top: 70px; left: 0; right: 0;
    text-align: center;
  }
  .person-name {
    display: inline-block;
    color: var(--red);
    font-weight: 700;
    font-size: 32px;
    letter-spacing: 0.5px;
    padding: 0 10px 6px;
    border-bottom: 1.5px solid var(--red);
  }
  .person-title {
    color: var(--orange);
    font-size: 15px;
    font-weight: 500;
    margin-top: 4px;
    letter-spacing: 0.5px;
  }
  .contact-block {
    position: absolute;
    left: 0; right: 0; bottom: 110px;
    text-align: center;
    color: var(--ink);
    font-size: 15px;
    line-height: 1.35;
  }
  .brand-square {
    display: block;
    width: 40px; height: 40px;
    margin: 0 auto 18px;
    background: var(--yellow);
  }
  .contact-group + .contact-group { margin-top: 14px; }
  .brand-name {
    color: var(--red);
    font-weight: 500;
    font-size: 58px;
    letter-spacing: -0.5px;
  }
</style>
</head>
<body>
  <section class="card card-front" aria-label="Business card front">
    <div class="name-block">
      <div class="person-name">Gordon Pratley</div>
      <div class="person-title">Chairman</div>
    </div>
    <div class="contact-block">
      <span class="brand-square" aria-hidden="true"></span>
      <div class="contact-group">
        <div>(C)813-555-4172 (F)813-555-8036</div>
        <div>gpratley@brindlestaffing.com</div>
      </div>
      <div class="contact-group">
        <div>417 39th Avenue South</div>
        <div>SAINT PETERSBURG FL 33712</div>
        <div>www.brindlestaffing.com</div>
      </div>
    </div>
  </section>

  <section class="card card-back" aria-label="Business card back">
    <div class="brand-name">BrindleStaffing</div>
  </section>
</body>
</html>
```